TA BRAMLEY BUSINESS CARD DESIGN PROJECT

We need to utilize our logo that was expertly created on PixelHarbor and now need to match this with a business card design.

```html
<!DOCTYPE html>
<html lang="en">
<head>
<meta charset="UTF-8">
<title>TA Bramley Business Card</title>
<link href="https://fonts.googleapis.com/css2?family=Open+Sans:wght@400;700&display=swap" rel="stylesheet">
<style>
  :root {
    --backdrop: #3b3b3b;
    --card: #161616;
    --blue: #1c5fc4;
    --text: #f2f2f2;
    --pattern-dark: #1d1d1d;
    --pattern-light: #2e2e2e;
  }
  * { box-sizing: border-box; margin: 0; padding: 0; }
  html, body {
    width: 1200px; height: 801px; overflow: hidden;
    background: var(--backdrop);
    font-family: "Open Sans", Arial, sans-serif;
  }
  .stage {
    position: relative; width: 1200px; height: 801px;
    display: flex; align-items: center; justify-content: center; gap: 60px;
  }
  .card {
    position: relative; width: 525px; height: 300px;
    background: var(--card);
    border-bottom: 3px solid var(--blue);
    border-left: 2px solid var(--blue);
    box-shadow: 0 18px 40px rgba(0,0,0,.45);
    overflow: hidden;
  }
  /* front */
  .brand-name {
    position: absolute; left: 34px; top: 98px;
    color: var(--blue); font-weight: 700; font-size: 26px; letter-spacing: 3px;
  }
  .holder {
    position: absolute; right: 34px; top: 30px; text-align: right;
  }
  .holder-name {
    color: var(--blue); font-weight: 700; font-size: 17px; letter-spacing: .5px;
  }
  .holder-role { color: var(--text); font-size: 12px; margin-top: 1px; }
  .rule-short {
    position: absolute; right: 30px; top: 82px; width: 215px; height: 1px; background: var(--blue);
  }
  .address {
    position: absolute; right: 34px; top: 96px; text-align: right;
    color: var(--text); font-size: 13px; line-height: 1.55;
  }
  .rule-long {
    position: absolute; left: 34px; right: 30px; top: 198px; height: 1px; background: var(--blue);
  }
  .contacts {
    position: absolute; left: 34px; top: 212px; list-style: none;
    color: var(--text); font-size: 13px; line-height: 1.6;
  }
  .contacts li { display: flex; align-items: center; gap: 8px; }
  .contacts svg { width: 11px; height: 11px; fill: var(--blue); flex: none; }
  /* back */
  .pattern-field {
    position: absolute; inset: 0;
    background: linear-gradient(120deg, var(--pattern-dark) 0%, var(--pattern-light) 100%);
  }
  .back-mark {
    position: absolute; left: 50%; top: 50%; transform: translate(-50%, -50%);
    color: var(--blue); font-weight: 700; font-size: 22px; letter-spacing: 3px;
    background: var(--card); padding: 6px 14px;
  }
</style>
</head>
<body>
<main class="stage">
  <section class="card card-front">
    <div class="brand-name">TA BRAMLEY</div>
    <div class="holder">
      <div class="holder-name">DORIAN VALE</div>
      <div class="holder-role">President</div>
    </div>
    <div class="rule-short"></div>
    <div class="address">1870 Cove Ridge Lane<br>Seabrook CA 90210</div>
    <div class="rule-long"></div>
    <ul class="contacts">
      <li><svg viewBox="0 0 24 24"><path d="M6.6 10.8a15 15 0 0 0 6.6 6.6l2.2-2.2c.3-.3.7-.4 1-.2 1.1.4 2.3.6 3.6.6.6 0 1 .4 1 1V20c0 .6-.4 1-1 1A17 17 0 0 1 3 4c0-.6.4-1 1-1h3.5c.6 0 1 .4 1 1 0 1.3.2 2.5.6 3.6.1.3 0 .7-.2 1z"/></svg>555-014-2087</li>
      <li><svg viewBox="0 0 24 24"><path d="M2 5h20v14H2z M2 5l10 8 10-8" /></svg>d.vale@tabramley.com</li>
      <li><svg viewBox="0 0 24 24"><circle cx="12" cy="12" r="10"/></svg>www.tabramley.com</li>
    </ul>
  </section>

  <section class="card card-back">
    <div class="pattern-field" role="img" aria-label="Repeating brand mark pattern in glossy black and charcoal"></div>
    <div class="back-mark">TA BRAMLEY</div>
  </section>
</main>
</body>
</html>
```